Website design and coding for new consultancy company

I need to have a full website designed for a new consultancy business I'm trying to establish. It's called BrightPath consult. I need an English version to begin with, and then there should be a Danish version as well, but I'll translate that myself. Just be aware that I need two language versions. The consultancy field that I'm targeting is Leadership - and specialist development. I offer to facilitate corporate academies for global companies as well as specific workshops within leadership- or team development, strategy sessions, personal coaching and facilitation of D&I (Diversity and inclusion) workshops. BTW my logo is not in high resolution - I need that as well.

Target Market(s)

Larger companies that has a need for developing their inhouse leadership capabilities or that wants to develop their specialists to take on more responsibility.

Industry/Entity Type

Consultancy business

Coding

Coded - Design and coding required

Number of Pages Required

5+ page

Requirements
Must have
• Introduction site with a catch phrase. Book a meeting. Services that's beeing offered. Blog site with white papers etc. Language toggle (Danish/English). Cases/testimonials. About site. Contact site.

```html
<!DOCTYPE html>
<html lang="en">
<head>
<meta charset="utf-8">
<title>BrightPath consult</title>
<link href="https://fonts.googleapis.com/css2?family=Manrope:wght@400;500;600;700;800&display=swap" rel="stylesheet">
<style>
:root{
  --blue:#2f7fc0;
  --blue-dark:#1f5f96;
  --ink:#1c1c1c;
  --topbar:#161616;
  --pale:#eef6fc;
  --line:#9cc4e4;
  --white:#fff;
}
*{box-sizing:border-box;margin:0;padding:0}
html,body{width:1200px;height:3602px;overflow:hidden}
body{font-family:'Manrope',sans-serif;color:var(--ink);background:var(--white);position:relative}
.abs{position:absolute}
svg{display:block}

/* top bar */
.topbar{left:0;top:0;width:1200px;height:54px;background:var(--topbar);color:#eee;font-size:15px}
.topbar .item{display:flex;align-items:center;gap:12px;top:17px}
.topbar .divider{left:580px;top:12px;width:1px;height:28px;background:#777}
.social{display:flex;gap:10px}
.social span{width:16px;height:16px;border-radius:50%;background:var(--blue);display:block}

/* nav */
.nav{left:0;top:54px;width:1200px;height:86px;background:#fff;box-shadow:0 1px 4px rgba(0,0,0,.06)}
.logo{font-weight:800;color:var(--blue-dark);font-size:30px;letter-spacing:-.5px;display:flex;align-items:center;gap:10px}
.logo i{width:14px;height:14px;background:var(--blue);display:block}
.nav .links{left:366px;top:31px;display:flex;gap:31px;font-size:16px;font-weight:500}
.nav .links .active{color:var(--blue)}
.btn{display:flex;align-items:center;justify-content:center;gap:12px;border-radius:3px;font-size:16px;font-weight:500;background:var(--blue);color:#fff;box-shadow:0 3px 6px rgba(0,0,0,.18)}
.btn.light{background:#fff;color:var(--blue)}
.btn.ghost{background:transparent;border:1.5px solid #fff;box-shadow:none}

/* hero */
.hero{left:0;top:140px;width:1200px;height:526px;background:linear-gradient(90deg,#2b6fad 0%,#4f86b8 40%,#9fb7cf 62%,#c8d3dc 78%,#7f9bb8 100%)}
.hero h1{left:112px;top:140px;color:#fff;font-size:44px;font-weight:600;line-height:48px;letter-spacing:-.5px}
.hero p{left:112px;top:256px;width:470px;color:#fff;font-size:16px;line-height:27px}

/* headings */
.section-title{font-size:39px;font-weight:600;color:var(--blue);letter-spacing:-.5px}
.body-text{font-size:15.5px;line-height:26px}

/* about */
.about-sub{left:112px;top:858px;font-size:26px;font-weight:600;color:var(--blue)}
.about-copy{left:112px;top:912px;width:520px}
.about-copy p+p{margin-top:25px}
.portrait{left:719px;top:783px;width:368px;height:442px;background:linear-gradient(180deg,#f4f6f8 0%,#e8ebee 55%,#3b4a66 100%);box-shadow:6px 6px 10px rgba(47,127,192,.35)}
.caption{left:734px;top:1172px;width:336px;height:39px;background:#fff;border-radius:2px;display:flex;align-items:center;justify-content:center;font-size:15px;box-shadow:0 2px 5px rgba(0,0,0,.1)}
.caption b{color:var(--blue);font-weight:500;margin-right:5px;font-size:17px}

/* services */
.services{left:0;top:1336px;width:1200px;height:888px;background:var(--pale)}
.center{width:1200px;left:0;text-align:center}
.card-img{width:312px;height:343px;border-radius:6px}
.card-label{height:40px;background:#fff;border-radius:2px;display:flex;align-items:center;justify-content:center;font-size:17px;color:var(--blue);font-weight:500;box-shadow:0 2px 5px rgba(0,0,0,.08)}
.card-text{width:312px;text-align:center;font-size:15.5px;line-height:26px}
.card-frame{left:445px;top:1594px;width:312px;height:515px;border:1.5px solid var(--line);border-radius:6px}

/* why */
.why-box{left:56px;top:2520px;width:1088px;height:261px;border:1.5px solid var(--line);border-radius:6px}
.why-icon{width:84px;height:84px;border-radius:50%;background:var(--blue);display:flex;align-items:center;justify-content:center}
.why-title{width:260px;text-align:center;font-size:20px;font-weight:500;color:var(--blue)}
.why-text{width:230px;text-align:center;font-size:14.5px;line-height:25px}

/* contact band */
.cta{left:0;top:2910px;width:1200px;height:339px;background:linear-gradient(90deg,#2b6fad 0%,#4a7eae 45%,#7c8f94 75%,#b39b61 100%)}
.cta h2{left:112px;top:78px;color:#fff;font-size:40px;font-weight:600}
.cta p{left:110px;top:140px;color:#fff;font-size:20px;line-height:33px}

/* footer */
.footer-links{top:3396px;display:flex;justify-content:center;gap:34px;font-size:17px}
.footer-contact{top:3452px;display:flex;justify-content:center;align-items:center;gap:30px;font-size:15px}
.copyright{top:3552px;font-size:12.5px;color:var(--blue)}
</style>
</head>
<body>

<!-- top bar -->
<div class="abs topbar">
  <div class="abs item" style="left:415px">
    <svg width="18" height="18" viewBox="0 0 24 24" fill="none" stroke="#5b9bd5" stroke-width="1.8"><path d="M5 3h4l2 5-3 2a11 11 0 0 0 6 6l2-3 5 2v4a2 2 0 0 1-2 2A17 17 0 0 1 3 5a2 2 0 0 1 2-2z"/></svg>
    +45 2000 1100
  </div>
  <div class="abs divider"></div>
  <div class="abs item" style="left:609px">
    <svg width="18" height="14" viewBox="0 0 24 18" fill="none" stroke="#5b9bd5" stroke-width="1.8"><rect x="1" y="1" width="22" height="16" rx="1"/><path d="M1 2l11 8 11-8"/></svg>
    hello@brightpath.example
  </div>
  <div class="abs item" style="left:902px">Follow us
    <div class="social"><span></span><span></span><span></span><span></span></div>
  </div>
</div>

<!-- nav -->
<div class="abs nav">
  <div class="abs logo" style="left:112px;top:24px"><i></i>BrightPath</div>
  <div class="abs links"><span class="active">Home</span><span>About Us</span><span>Services</span><span>Why Choose Us</span><span>Contact Us</span></div>
  <div class="abs btn" style="left:940px;top:24px;width:148px;height:37px">Get in Touch <span>→</span></div>
</div>

<!-- hero -->
<section class="abs hero" role="img" aria-label="Photo of three colleagues reviewing a tablet in a bright office">
  <h1 class="abs">Elevate Leadership.<br>Empower Organizations.</h1>
  <p class="abs">Unlock the full potential of your leaders and teams with bespoke development programs, strategic workshops, and expert coaching designed for global impact.</p>
  <div class="abs btn light" style="left:112px;top:375px;width:188px;height:37px">Discover Services <span>→</span></div>
</section>

<!-- about -->
<h2 class="abs section-title" style="left:176px;top:788px">About Us</h2>
<div class="abs about-sub">Empower Teams. Transform Organizations.</div>
<div class="abs about-copy body-text">
  <p>At BrightPath consult, we specialize in cultivating exceptional leadership and fostering specialist talent across industries worldwide.</p>
  <p>With deep expertise in corporate academies, leadership workshops, and diversity &amp; inclusion facilitation, we partner with organizations to drive meaningful change, create resilient teams, and accelerate growth.</p>
  <p>Our approach combines proven methodologies with tailored solutions to meet your unique business challenges.</p>
</div>
<div class="abs btn" style="left:115px;top:1186px;width:147px;height:36px">Learn More <span>→</span></div>
<div class="abs portrait" role="img" aria-label="Portrait of the company founder in a suit"></div>
<div class="abs caption"><b>Mark Jensen,</b> CEO - BrightPath consult</div>

<!-- services -->
<section class="abs services"></section>
<h2 class="abs section-title center" style="top:1410px">Services We Offer</h2>
<p class="abs center body-text" style="top:1484px">Our approach combines proven methodologies with tailored solutions to<br>meet your unique business challenges.</p>

<svg class="abs" style="left:40px;top:1740px" width="18" height="30" viewBox="0 0 18 30" fill="none" stroke="#2f7fc0" stroke-width="2.5"><path d="M15 2L3 15l12 13"/></svg>
<svg class="abs" style="left:1136px;top:1740px" width="18" height="30" viewBox="0 0 18 30" fill="none" stroke="#2f7fc0" stroke-width="2.5"><path d="M3 2l12 13L3 28"/></svg>

<div class="abs card-frame"></div>
<div class="abs card-img" style="left:112px;top:1594px;background:linear-gradient(160deg,#cfd8e0,#5d6c7d)" role="img" aria-label="Photo of a trainer presenting to a corporate group"></div>
<div class="abs card-img" style="left:445px;top:1592px;background:linear-gradient(160deg,#e1e6ea,#8f8a80)" role="img" aria-label="Photo of a facilitator leading a team workshop"></div>
<div class="abs card-img" style="left:775px;top:1592px;background:linear-gradient(160deg,#d3dae0,#4f5d6e)" role="img" aria-label="Photo of a strategy coaching session with a presenter"></div>
<div class="abs card-label" style="left:125px;top:1916px;width:286px">Corporate Academies</div>
<div class="abs card-label" style="left:458px;top:1916px;width:286px">Leadership &amp; Team Workshops</div>
<div class="abs card-label" style="left:788px;top:1916px;width:286px">Strategy Coaching Sessions</div>
<p class="abs card-text" style="left:112px;top:1987px">Tailored leadership development<br>programs designed to nurture the next<br>generation of leaders.</p>
<p class="abs card-text" style="left:445px;top:1987px">Interactive sessions focused on<br>enhancing leadership thinking to drive<br>performance and engagement.</p>
<p class="abs card-text" style="left:775px;top:1987px">Interactive sessions focused on<br>enhancing leadership thinking to drive<br>performance and engagement.</p>
<div class="abs btn" style="left:526px;top:2090px;width:148px;height:36px">Learn More <span>→</span></div>

<!-- why choose us -->
<h2 class="abs section-title center" style="top:2292px">Why Choose Us</h2>
<p class="abs center body-text" style="top:2376px">At BrightPath consult, we specialize in cultivating exceptional leadership<br>and fostering specialist talent across industries worldwide.</p>
<div class="abs why-box"></div>

<div class="abs why-icon" style="left:178px;top:2477px"><svg width="40" height="40" viewBox="0 0 24 24" fill="none" stroke="#fff" stroke-width="1.5"><circle cx="12" cy="12" r="10"/><path d="M2 12h20M12 2c3 3 3 17 0 20M12 2c-3 3-3 17 0 20"/></svg></div>
<div class="abs why-icon" style="left:435px;top:2477px;box-shadow:0 0 0 4px #fff,0 0 0 5.5px var(--blue)"><svg width="40" height="40" viewBox="0 0 24 24" fill="none" stroke="#fff" stroke-width="1.5"><rect x="6" y="3" width="15" height="15" rx="1"/><path d="M3 7v14h14M9 7h4v4H9zM15 7h3M15 10h3M9 14h9"/></svg></div>
<div class="abs why-icon" style="left:694px;top:2477px"><svg width="40" height="40" viewBox="0 0 24 24" fill="#fff"><rect x="4" y="12" width="2.5" height="7"/><rect x="8.5" y="9" width="2.5" height="10"/><rect x="13" y="11" width="2.5" height="8"/><rect x="17.5" y="6" width="2.5" height="13"/><rect x="3" y="20" width="18" height="1.2"/></svg></div>
<div class="abs why-icon" style="left:943px;top:2477px"><svg width="42" height="42" viewBox="0 0 24 24" fill="none" stroke="#fff" stroke-width="1.5"><circle cx="12" cy="10" r="2.5"/><circle cx="6" cy="12" r="2"/><circle cx="18" cy="12" r="2"/><path d="M8 19a4 4 0 0 1 8 0M2.5 19a3.5 3.5 0 0 1 5-3M21.5 19a3.5 3.5 0 0 0-5-3M4 8a6 6 0 0 1 8-4 6 6 0 0 1 8 4"/></svg></div>

<div class="abs why-title" style="left:90px;top:2587px">Proven Global Expertise</div>
<div class="abs why-title" style="left:350px;top:2587px">Customized Programs</div>
<div class="abs why-title" style="left:605px;top:2587px">Measurable Outcomes</div>
<div class="abs why-title" style="left:855px;top:2587px">Culture Inclusive</div>
<p class="abs why-text" style="left:105px;top:2629px">Decades of consulting with leading companies worldwide. Tailored solutions for diverse industries and cultures.</p>
<p class="abs why-text" style="left:362px;top:2629px">Personalized leadership and team growth journeys. Designed to meet your unique organizational goals.</p>
<p class="abs why-text" style="left:620px;top:2629px">Focused on driving tangible, lasting results. Improving leadership effectiveness and team performance.</p>
<p class="abs why-text" style="left:869px;top:2629px">Expert facilitation in Diversity &amp; Inclusion. Building equitable and thriving workplace environments.</p>
<div class="abs btn" style="left:404px;top:2764px;width:148px;height:36px">Learn More <span>→</span></div>

<!-- contact band -->
<section class="abs cta" role="img" aria-label="Photo of a city skyline with office towers at sunset">
  <h2 class="abs">Get in Touch</h2>
  <p class="abs">Ready to elevate your leadership and<br>specialist development? Let's connect.</p>
  <div class="abs btn ghost" style="left:111px;top:220px;width:147px;height:37px">Contact Us <span>→</span></div>
</section>

<!-- footer -->
<div class="abs logo center" style="top:3306px;justify-content:center;font-size:34px"><i></i>BrightPath</div>
<nav class="abs center footer-links"><span>Home</span><span>About Us</span><span>Services</span><span>Why Choose Us</span><span>Contact Us</span></nav>
<div class="abs center footer-contact">
  <span style="display:flex;gap:12px;align-items:center"><svg width="18" height="18" viewBox="0 0 24 24" fill="none" stroke="#2f7fc0" stroke-width="1.8"><path d="M5 3h4l2 5-3 2a11 11 0 0 0 6 6l2-3 5 2v4a2 2 0 0 1-2 2A17 17 0 0 1 3 5a2 2 0 0 1 2-2z"/></svg>+45 2000 1100</span>
  <span style="width:1px;height:28px;background:#bbb"></span>
  <span style="display:flex;gap:12px;align-items:center"><svg width="18" height="14" viewBox="0 0 24 18" fill="none" stroke="#2f7fc0" stroke-width="1.8"><rect x="1" y="1" width="22" height="16" rx="1"/><path d="M1 2l11 8 11-8"/></svg>hello@brightpath.example</span>
</div>
<div class="abs center" style="top:3505px;display:flex;justify-content:center;align-items:center;gap:14px;font-size:15px">Follow us
  <div class="social"><span style="width:18px;height:18px"></span><span style="width:18px;height:18px"></span><span style="width:18px;height:18px"></span><span style="width:18px;height:18px"></span></div>
</div>
<div class="abs center copyright">© 2025 BrightPath consult. All Rights Reserved.</div>

</body>
</html>
```